Dorwin's Coating & Renewal Letterhead Design We want to revamp out old traditional letterhead with the new logo designs that are attached. We are working on getting all our company items from vehicles, business, cards, t-shirts, letterhead to match. This should include company colors, fonts, and flow of items that we have attached below.

Industry/Entity Type

Construction Company

Font styles to use
Sans Serif
Other font styles liked:
• Bold with outline

Colors
ec1f27
ffffff

Requirements
Must have
• Company Name: Dorwin's Coating & Renewal
• Address: 4728 SW 81st Ter Halverd cove fl 39417
• Office Number: (555) 413-2986
• Email: Dorwinrenewal@mailbrook.example
• License Number: KRT8046392
Nice to have
• Company Colors: red, white, black, and grey

```html
<!DOCTYPE html>
<html lang="en">
<head>
<meta charset="utf-8">
<title>Dorwin's Coating &amp; Renewal — Letterhead</title>
<link rel="stylesheet" href="https://fonts.googleapis.com/css2?family=Arimo:wght@400;700&family=Tinos:wght@400;700&display=swap">
<style>
  :root {
    --brand-red: #ec1f27;
    --deep-red: #a3161d;
    --ink-black: #111111;
    --stripe-grey: #9a9a9a;
    --stripe-light: #cfcfcf;
    --body-grey: #7a7a7a;
    --paper: #ffffff;
    --backdrop: #d9dcdd;
  }
  * { margin: 0; padding: 0; box-sizing: border-box; }
  html, body {
    width: 1200px; height: 784px; overflow: hidden;
    background: var(--backdrop);
  }
  .letterhead {
    position: absolute; left: 331px; top: 12px;
    width: 537px; height: 760px;
    background: var(--paper);
    box-shadow: 0 2px 10px rgba(0,0,0,.15);
    overflow: hidden;
  }
  .corner { position: absolute; }
  .corner--top-right { right: 0; top: 0; }
  .corner--bottom-left { left: 0; bottom: 0; }

  .brand {
    position: absolute; left: 40px; top: 42px;
    display: flex; align-items: center; gap: 7px;
  }
  .brand__mark { width: 12px; height: 12px; background: var(--brand-red); }
  .brand__name {
    font-family: "Arimo", Arial, sans-serif; font-weight: 700;
    font-size: 16px; color: var(--brand-red); letter-spacing: .1px;
    white-space: nowrap;
  }
  .contact {
    position: absolute; left: 298px; top: 32px;
    font-family: "Tinos", "Times New Roman", serif;
    font-size: 8px; line-height: 11.5px; color: var(--body-grey);
    list-style: none; white-space: nowrap;
  }
  .contact li { display: flex; align-items: flex-start; gap: 5px; }
  .contact__icon {
    flex: none; width: 8px; height: 8px; margin-top: 1.8px;
    border-radius: 50%; background: var(--brand-red);
    display: flex; align-items: center; justify-content: center;
  }
  .contact__address { color: var(--brand-red); font-weight: 700; }

  .letter-body {
    position: absolute; left: 64px; top: 110px; width: 392px;
    font-family: "Arimo", Arial, sans-serif;
    font-size: 9.6px; line-height: 13.4px; color: var(--body-grey);
  }
  .letter-body p { margin-bottom: 13px; }
  .signature {
    position: absolute; left: 150px; top: 450px;
    width: 150px; height: 56px; border-radius: 4px;
    background: linear-gradient(90deg, rgba(150,150,150,.12), rgba(150,150,150,.28), rgba(150,150,150,.12));
  }
</style>
</head>
<body>
<main class="letterhead">
  <svg class="corner corner--top-right" width="150" height="240" viewBox="0 0 150 240" aria-hidden="true">
    <defs>
      <linearGradient id="redFadeTop" x1="1" y1="0" x2="0" y2="1">
        <stop offset="0" stop-color="var(--deep-red)"/>
        <stop offset="1" stop-color="var(--brand-red)"/>
      </linearGradient>
    </defs>
    <polygon points="84,0 150,0 150,240" fill="var(--stripe-grey)"/>
    <polygon points="94,0 150,0 150,240" fill="var(--ink-black)"/>
    <polygon points="102,0 150,0 150,240" fill="var(--stripe-light)"/>
    <polygon points="108,0 150,0 150,240" fill="url(#redFadeTop)"/>
  </svg>

  <svg class="corner corner--bottom-left" width="150" height="240" viewBox="0 0 150 240" aria-hidden="true">
    <defs>
      <linearGradient id="redFadeBottom" x1="0" y1="1" x2="1" y2="0">
        <stop offset="0" stop-color="var(--deep-red)"/>
        <stop offset="1" stop-color="var(--brand-red)"/>
      </linearGradient>
    </defs>
    <polygon points="0,0 66,240 0,240" fill="var(--stripe-grey)"/>
    <polygon points="0,0 56,240 0,240" fill="var(--ink-black)"/>
    <polygon points="0,0 48,240 0,240" fill="var(--stripe-light)"/>
    <polygon points="0,0 42,240 0,240" fill="url(#redFadeBottom)"/>
  </svg>

  <header class="brand">
    <span class="brand__mark"></span>
    <span class="brand__name">Dorwin's Coating &amp; Renewal</span>
  </header>

  <ul class="contact">
    <li><span class="contact__icon"><svg width="5" height="6" viewBox="0 0 10 12"><path d="M5 0a4 4 0 0 1 4 4c0 3-4 8-4 8S1 7 1 4a4 4 0 0 1 4-4z" fill="#fff"/></svg></span>
      <span class="contact__address">4728 SW 81st Ter<br>Halverd cove fl 39417</span></li>
    <li><span class="contact__icon"><svg width="5" height="5" viewBox="0 0 10 10"><path d="M2 0l2 2-1 2 3 3 2-1 2 2-2 2C4 10 0 6 0 2z" fill="#fff"/></svg></span>(555) 413-2986</li>
    <li><span class="contact__icon"><svg width="5" height="5" viewBox="0 0 10 10"><path d="M1 5l3 3 5-6" stroke="#fff" stroke-width="2" fill="none"/></svg></span>License: KRT8046392</li>
    <li><span class="contact__icon"><svg width="5" height="4" viewBox="0 0 10 8"><rect x="0" y="0" width="10" height="8" fill="#fff"/></svg></span>Dorwinrenewal@mailbrook.example</li>
    <li><span class="contact__icon"></span>www.dorwinrenewal.example</li>
  </ul>

  <article class="letter-body">
    <p>Lorem Ipsum is simply dummy text of the printing and typesetting industry. Lorem Ipsum has been the industry's standard dummy text ever since the 1500s, when an unknown printer took a galley of type and scrambled it to make a type specimen book. It has survived not only five centuries, but also the leap into electronic typesetting, remaining essentially unchanged. It was popularised in the 1960s with the release of Transfera sheets containing Lorem Ipsum passages, and more recently with desktop publishing software like Pagewright including versions of Lorem Ipsum.</p>
    <p>It is a long established fact that a reader will be distracted by the readable content of a page when looking at its layout. The point of using Lorem Ipsum is that it has a more-or-less normal distribution of letters, as opposed to using 'Content here, content here', making it look like readable English. Many desktop publishing packages and web page editors now use Lorem Ipsum as their default model text, and a search for 'lorem ipsum' will uncover many web sites still in their infancy. Various versions have evolved over the years, sometimes by accident, sometimes on purpose (injected humour and the like).</p>
    <p>Contrary to popular belief, Lorem Ipsum is not simply random text. It has roots in a piece of classical Latin literature from 45 BC, making it over 2000 years old. Halvard Metcalfe, a Latin professor at Ashgrove College in Virginia, looked up one of the more obscure Latin words, consectetur, from a Lorem Ipsum passage, and going through the cites of the word in classical literature, discovered the undoubtable source. Lorem Ipsum comes from sections 1.10.32 and 1.10.33 of "de Finibus Bonorum et Malorum" structures, to generate Lorem Ipsum which looks reasonable. The generated Lorem Ipsum is therefore always free from repetition, injected humour, or non-characteristic words etc.</p>
  </article>

  <div class="signature" role="img" aria-label="Handwritten signature of the sender"></div>
</main>
</body>
</html>
```